Ad for Cyber Security Company- Print Ad

We are looking for an awesome designer to create a one page advertisement for the Kelvora Security data analytics platform that will be featured in an upcoming security magazine. This is also going to be featured in an upcoming trade show. Kelvora Security produced the KELVORA platform to help companies unify their security environment and help them address Insider Threat, Fraud and Anomaly ID and resolution. KELVORA uses an an advanced ingestion engine, machine learning, and workflow automation to ensure the right people are getting the right info at the right time. We serve enterprise level customers, augmenting and enhancing, not replacing their existing security stack. We would like few or single image, clean, and open ad built around the tagline 'Make Security a Team Sport.' We would like the logo to be featured, and include our website address on the page (www.kelvorasecurity.net). See below for style guide.

Target Market(s)

Industry insiders, Chief Information Security Officers (CISO) and Technical directors.

Other font styles liked:
• See style guide, but we are open to suggestion.

Requirements
Must have
• A single image (minimum), Feature the provided logo, Include the tagline 'Make Security a Team Sport' and have the website somewhere on the ad. The image should focus on the conveying the message of "Make Security a Team Sport" and not be a generic security (padlock, network, etc.) image.
• See included style guide.

```html
<!DOCTYPE html>
<html lang="en">
<head>
<meta charset="utf-8">
<title>Kelvora Security – Make Security a Team Sport</title>
<link rel="stylesheet" href="https://fonts.googleapis.com/css2?family=Open+Sans:wght@400;600;700;800&family=Ubuntu:wght@700&display=swap">
<style>
  :root {
    --orange: #f26522;
    --charcoal: #3b3b3b;
    --charcoal-light: #5a5a5a;
    --ink: #111111;
    --paper: #ffffff;
    --stage: #c8c8c8;
    --text-dark: #2b2b2b;
  }
  * { box-sizing: border-box; margin: 0; padding: 0; }
  html, body { width: 1200px; height: 1200px; overflow: hidden; background: var(--stage); }
  .flyer {
    position: absolute; left: 155px; top: 28px;
    width: 742px; height: 954px;
    transform: scale(1.2); transform-origin: top left;
    font-family: "Open Sans", sans-serif;
    overflow: hidden;
  }
  .flyer-art { position: absolute; inset: 0; width: 742px; height: 954px; }
  .brand {
    position: absolute; left: 28px; top: 36px;
    display: flex; align-items: center; gap: 12px;
    color: var(--orange); font-weight: 800; font-size: 34px;
    letter-spacing: 1px; line-height: 1;
  }
  .brand-dot { width: 22px; height: 22px; border-radius: 50%; background: var(--orange); }
  .tagline {
    position: absolute; right: 30px; top: 392px;
    font-family: "Ubuntu", sans-serif; font-weight: 700;
    color: var(--paper); font-size: 42px; line-height: 52px; text-align: center;
  }
  .intro-panel { position: absolute; left: 28px; top: 576px; width: 296px; color: var(--paper); }
  .intro-lead { font-size: 16.5px; line-height: 20px; text-align: justify; margin-bottom: 18px; }
  .intro-panel p.body { font-size: 11.6px; line-height: 14.2px; text-align: justify; margin-bottom: 14px; }
  .about-tab {
    position: absolute; left: 582px; top: 560px; width: 160px; height: 40px;
    background: var(--orange); border-radius: 20px 0 0 20px;
    font-family: "Ubuntu", sans-serif; font-weight: 700; color: var(--paper);
    font-size: 21px; line-height: 40px; text-align: center;
  }
  .about-text { position: absolute; left: 362px; top: 620px; width: 353px; color: var(--text-dark); }
  .about-text p { font-size: 11.6px; line-height: 14.2px; text-align: justify; margin-bottom: 12px; }
  .footer-phone {
    position: absolute; left: 28px; top: 895px;
    display: flex; align-items: center; gap: 7px;
    font-family: "Ubuntu", sans-serif; font-weight: 700; color: var(--text-dark); font-size: 21px;
  }
  .footer-phone svg { width: 17px; height: 17px; }
  .footer-contact { position: absolute; left: 380px; top: 886px; color: var(--paper); font-size: 16px; line-height: 21px; }
  .footer-contact li { list-style: none; display: flex; align-items: center; gap: 9px; }
  .footer-contact svg { width: 13px; height: 13px; }
  .social { position: absolute; left: 652px; top: 896px; display: flex; gap: 8px; }
  .social span { width: 26px; height: 26px; border-radius: 50%; background: var(--paper); }
</style>
</head>
<body>
<div class="flyer">
  <svg class="flyer-art" viewBox="0 0 742 954">
    <defs>
      <linearGradient id="photoTone" x1="0" y1="0" x2="1" y2="0.35">
        <stop offset="0" stop-color="#5b7a99"/>
        <stop offset="0.45" stop-color="#2a3646"/>
        <stop offset="1" stop-color="#111111"/>
      </linearGradient>
      <linearGradient id="screenTone" x1="0" y1="0" x2="0" y2="1">
        <stop offset="0" stop-color="#2a2a2a"/>
        <stop offset="0.72" stop-color="#5e5e5e"/>
        <stop offset="0.73" stop-color="#d9d9d9"/>
        <stop offset="1" stop-color="#9a9a9a"/>
      </linearGradient>
    </defs>
    <rect class="backdrop" width="742" height="954" fill="var(--charcoal)"/>
    <path class="hero-band" d="M0,110 L742,110 L742,505 C380,580 140,530 0,380 Z" fill="var(--ink)"/>
    <path class="hero-photo" role="img" aria-label="Photo of a hooded analyst at a laptop surrounded by glowing network icons"
          d="M0,110 L340,110 C325,230 380,320 480,350 L480,560 C300,560 130,500 0,370 Z" fill="url(#photoTone)"/>
    <path class="monitor-field" d="M470,0 L742,0 L742,366 C450,378 300,180 470,2 Z" fill="var(--charcoal)"/>
    <path class="monitor-arc-gray" d="M460,4 C290,190 450,392 742,380" fill="none" stroke="var(--charcoal-light)" stroke-width="6"/>
    <path class="monitor-arc" d="M470,2 C300,180 450,378 742,366" fill="none" stroke="var(--orange)" stroke-width="6"/>
    <rect class="dashboard-screen" role="img" aria-label="Desktop monitor showing the platform's analytics dashboard with a line chart"
          x="410" y="76" width="305" height="246" rx="6" fill="url(#screenTone)"/>
    <path class="swoosh-orange" d="M0,364 C140,514 380,566 742,491 L742,954 L0,954 Z" fill="var(--orange)"/>
    <path class="swoosh-gray" d="M0,372 C140,522 380,573 742,498 L742,954 L0,954 Z" fill="var(--charcoal-light)"/>
    <path class="lower-field" d="M0,380 C140,530 380,580 742,505 L742,954 L0,954 Z" fill="var(--charcoal)"/>
    <path class="lower-white" d="M742,505 C620,540 470,562 340,562 L340,954 L742,954 Z" fill="var(--paper)"/>
    <path class="lower-line" d="M380,560 C520,555 640,530 742,500" fill="none" stroke="var(--orange)" stroke-width="2"/>
    <path class="intro-corner" d="M340,560 L340,798 Q340,838 300,838 L0,838 L0,954 L340,954 Z" fill="var(--paper)"/>
    <path class="header-stripe" d="M0,0 L496,0 C432,104 300,148 0,140 Z" fill="var(--orange)"/>
    <path class="header-white" d="M0,0 L482,0 C420,94 300,140 0,134 Z" fill="var(--paper)"/>
    <rect class="footer-band" x="0" y="932" width="742" height="22" fill="var(--orange)"/>
    <path class="footer-block" d="M384,882 L742,882 L742,954 L360,954 L360,906 Q360,882 384,882 Z" fill="var(--orange)"/>
  </svg>

  <div class="brand"><span class="brand-dot"></span>KELVORA SECURITY</div>

  <h1 class="tagline">Make Security<br>a Team Sport</h1>

  <div class="intro-panel">
    <p class="intro-lead">KELVORA is a security data analytics platform, enabling security teams and business partners with timely, actionable alerts and intelligence.</p>
    <p class="body">KELVORA moves as fast as you. With a variety of deployment models including on-premises, hybrid, or fully cloud-based, clients measure ROI in weeks, not months.</p>
    <p class="body">KELVORA makes security a team sport. Leveraging advanced machine learning and workflow optimization, KELVORA ensures that the right information is making it to the right people every time.</p>
  </div>

  <h2 class="about-tab">About Us</h2>
  <div class="about-text">
    <p>KELVORA security data analytics platform that will be featured in an upcoming security magazine. This is also going to be featured in an upcoming trade show.</p>
    <p>Kelvora Security produced the KELVORA platform to help companies unify their security environment and help them address Insider Threat, Fraud and Anomaly ID and resolution.</p>
    <p>KELVORA uses an an advanced ingestion engine, machine learning, and workflow automation to ensure the right people are getting the right info at the right time. We serve enterprise level customers, augmenting and enhancing, not replacing their existing security stack.</p>
    <p>KELVORA complements existing tools, including SIEM and UBA, to provide enhanced visibility into your organization’s blind spots.</p>
  </div>

  <div class="footer-phone">
    <svg viewBox="0 0 20 20"><circle cx="10" cy="10" r="10" fill="var(--orange)"/><path d="M6.5,5 L8.5,5 L9.3,7.6 L8,8.6 C8.7,10 10,11.3 11.4,12 L12.4,10.7 L15,11.5 L15,13.5 C15,14.3 14.3,15 13.5,15 C9.4,14.7 5.3,10.6 5,6.5 C5,5.7 5.7,5 6.5,5 Z" fill="#fff"/></svg>
    IPSUM QUIA DOLOR
  </div>

  <ul class="footer-contact">
    <li><svg viewBox="0 0 14 14"><circle cx="7" cy="7" r="6" fill="none" stroke="#fff" stroke-width="1.6"/><path d="M4,5.5 L7,7.8 L10,5.5" fill="none" stroke="#fff" stroke-width="1.4"/></svg>ipsumquiadolorsitamet</li>
    <li><svg viewBox="0 0 14 14"><circle cx="7" cy="7" r="6" fill="none" stroke="#fff" stroke-width="1.2"/><ellipse cx="7" cy="7" rx="2.6" ry="6" fill="none" stroke="#fff" stroke-width="1"/><path d="M1,7 H13 M2,4 H12 M2,10 H12" stroke="#fff" stroke-width="0.9"/></svg>www.kelvorasecurity.net</li>
  </ul>

  <div class="social"><span></span><span></span></div>
</div>
</body>
</html>
```